Business card design needed

I need a business card design for a new online retail business based in Australia. I am unsure of the exact content of what I will be selling but it will be probably women's clothing, accessories, gym wear, gifts and maybe homeware linen. I am wanting a classy design that portrays the image of class/style/upmarket.

Target Market(s)

predominantely women - 20-50 age group

Industry/Entity Type

Retail

Contact Information for Business Card

Quietly Golden
Renata Calloway
Director
ABN 73418250964
17 Harrow Crescent Linfield Park NSW 2391
ph: +61 427 905 184
sales@quietlygolden.com.au

Logo Text

I am open for suggestions here

Requirements
Must have
• The design must be both sides of the card

```html
<!DOCTYPE html>
<html lang="en">
<head>
<meta charset="utf-8">
<title>Quietly Golden – Business Card</title>
<link rel="stylesheet" href="https://fonts.googleapis.com/css2?family=Arimo:wght@400&display=swap">
<style>
  :root {
    --page-bg: #f2f2f2;
    --lime: #a9d25c;
    --lime-light: #c4e27e;
    --green: #6cb33f;
    --green-deep: #0f7a35;
    --black: #050505;
    --charcoal: #1c1c1c;
    --graphite: #3b3b3b;
    --silver: #c9c9c9;
    --white: #ffffff;
    --text-grey: #d4d4d4;
  }
  html, body {
    margin: 0;
    padding: 0;
    width: 1200px;
    height: 900px;
    overflow: hidden;
    background: var(--page-bg);
    font-family: "Arimo", Arial, sans-serif;
  }
  .canvas {
    position: relative;
    width: 1200px;
    height: 900px;
  }
  .card {
    position: absolute;
    width: 560px;
    height: 330px;
    overflow: hidden;
    box-shadow: 0 6px 18px rgba(0,0,0,0.25);
  }
  .card svg.card-art {
    position: absolute;
    inset: 0;
    width: 100%;
    height: 100%;
  }
  .card-front { left: 90px; top: 100px; }
  .card-back  { left: 550px; top: 470px; }

  .front-brand {
    position: absolute;
    left: 0;
    right: 0;
    top: 190px;
    display: flex;
    justify-content: center;
    align-items: center;
    gap: 12px;
    color: var(--white);
    font-size: 34px;
    letter-spacing: 0.5px;
  }
  .brand-dot {
    width: 14px;
    height: 14px;
    border-radius: 50%;
    background: var(--green);
  }

  .brand-tile {
    position: absolute;
    left: 36px;
    top: 46px;
    width: 124px;
    height: 124px;
    background: linear-gradient(160deg, var(--green) 0%, var(--green-deep) 100%);
    display: flex;
    align-items: flex-end;
    justify-content: center;
    padding-bottom: 18px;
    box-sizing: border-box;
  }
  .brand-tile-name {
    color: var(--white);
    font-size: 15px;
  }

  .contact {
    position: absolute;
    left: 36px;
    top: 180px;
    color: var(--text-grey);
    font-size: 12px;
    line-height: 17px;
  }
  .contact-name {
    color: var(--lime);
    font-size: 20px;
    line-height: 24px;
  }
  .contact-role {
    font-size: 11px;
    margin-bottom: 9px;
  }
  .contact-address { margin-bottom: 9px; }
  .contact-line {
    display: flex;
    align-items: center;
    gap: 7px;
  }
  .contact-line svg { width: 11px; height: 11px; flex: none; }
</style>
</head>
<body>
<main class="canvas">

  <!-- Front of card -->
  <section class="card card-front" aria-label="Business card front">
    <svg class="card-art" viewBox="0 0 560 330" preserveAspectRatio="none" aria-hidden="true">
      <defs>
        <linearGradient id="front-green" x1="0" y1="1" x2="1" y2="0">
          <stop offset="0" stop-color="#9fcb55"/>
          <stop offset="0.6" stop-color="#b6dc72"/>
          <stop offset="1" stop-color="#0f7a35"/>
        </linearGradient>
        <linearGradient id="front-dark" x1="0.2" y1="1" x2="0.8" y2="0">
          <stop offset="0" stop-color="#000000"/>
          <stop offset="0.55" stop-color="#1d2110"/>
          <stop offset="1" stop-color="#8aa35a"/>
        </linearGradient>
      </defs>
      <rect width="560" height="330" fill="url(#front-green)"/>
      <ellipse cx="300" cy="210" rx="330" ry="250" fill="var(--silver)"/>
      <ellipse cx="300" cy="212" rx="322" ry="244" fill="url(#front-dark)"/>
    </svg>
    <div class="front-brand">
      <span class="brand-dot"></span>
      <span class="brand-name">Quietly Golden</span>
    </div>
  </section>

  <!-- Back of card -->
  <section class="card card-back" aria-label="Business card back">
    <svg class="card-art" viewBox="0 0 560 330" preserveAspectRatio="none" aria-hidden="true">
      <defs>
        <linearGradient id="back-dark" x1="0" y1="1" x2="1" y2="0">
          <stop offset="0" stop-color="#151515"/>
          <stop offset="0.6" stop-color="#222222"/>
          <stop offset="1" stop-color="#444444"/>
        </linearGradient>
      </defs>
      <rect width="560" height="330" fill="url(#back-dark)"/>
    </svg>

    <div class="brand-tile">
      <span class="brand-tile-name">Quietly Golden</span>
    </div>

    <div class="contact">
      <div class="contact-name">Renata Calloway</div>
      <div class="contact-role">Director</div>
      <div class="contact-address">
        ABN 73418250964 17 Harrow Crescent<br>
        Linfield Park NSW 2391
      </div>
      <div class="contact-line">
        <svg viewBox="0 0 12 12" aria-hidden="true"><path d="M2.5 1 L4.5 1 L5.3 3.4 L4 4.4 Q5 6.8 7.6 8 L8.6 6.7 L11 7.5 L11 9.5 Q10.5 11 9 11 Q1 10 1 2.8 Q1 1.2 2.5 1 Z" fill="var(--green)"/></svg>
        <span>+61 427 905 184</span>
      </div>
      <div class="contact-line">
        <svg viewBox="0 0 12 12" aria-hidden="true"><rect x="0.5" y="2" width="11" height="8" fill="var(--green)"/><path d="M0.5 2 L6 6.5 L11.5 2" fill="none" stroke="var(--charcoal)" stroke-width="1"/></svg>
        <span>sales@quietlygolden.com.au</span>
      </div>
    </div>
  </section>

</main>
</body>
</html>
```